DK Alarm 'Welcome' Envelope

I am looking for a 'Welcome' envelope design for new customers who sign up for our Alarm Services. In this envelope we will send confidential documents that the customer will need. I want it to stand out, yet look classy.

```html
<!DOCTYPE html>
<html lang="en">
<head>
<meta charset="utf-8">
<title>DK Alarm Welcome Envelope</title>
<link rel="stylesheet" href="https://fonts.googleapis.com/css2?family=Poppins:wght@300;400;700&display=swap">
<style>
  :root {
    --backdrop: #b3b3b3;
    --ink-deep: #03090c;
    --ink-teal: #04303d;
    --flap-teal: #06303d;
    --brand-green: #3fbf3a;
    --emblem-blue: rgba(10, 58, 92, 0.5);
    --emblem-green: rgba(30, 107, 42, 0.55);
    --text-light: #f2f5f6;
    --text-grey: #aab4b8;
    --stripe: rgba(175, 188, 194, 0.55);
  }
  * { margin: 0; padding: 0; box-sizing: border-box; }
  html, body { width: 1069px; height: 1200px; overflow: hidden; background: var(--backdrop); }
  .sheet { position: relative; width: 1069px; height: 1200px; font-family: "Poppins", sans-serif; }

  .envelope {
    position: absolute; left: 49px; overflow: hidden;
    background: radial-gradient(ellipse 60% 70% at 45% 45%, var(--ink-teal) 0%, #021a22 55%, var(--ink-deep) 100%);
  }
  .envelope--front { top: 80px; width: 924px; height: 502px; border-bottom: 3px solid #c9cdcf; }
  .envelope--back { top: 643px; width: 922px; height: 502px;
    background: radial-gradient(ellipse 45% 60% at 50% 50%, #043445 0%, #021c25 55%, var(--ink-deep) 100%); }

  .stripes {
    position: absolute;
    background: repeating-linear-gradient(to bottom, var(--stripe) 0 1.5px, transparent 1.5px 6px);
    -webkit-mask-image: linear-gradient(to bottom, transparent 0%, rgba(0,0,0,.35) 40%, #000 100%);
            mask-image: linear-gradient(to bottom, transparent 0%, rgba(0,0,0,.35) 40%, #000 100%);
  }
  .stripes--front { left: 0; right: 0; top: 358px; height: 140px; }
  .stripes--left { left: 0; width: 167px; top: 322px; height: 180px; }
  .stripes--right { right: 0; width: 166px; top: 322px; height: 180px; }

  .emblem-area {
    position: absolute;
    background: linear-gradient(to right, var(--emblem-blue) 0 50%, var(--emblem-green) 50% 100%);
    -webkit-mask-image: linear-gradient(to bottom, #000 60%, transparent 100%);
            mask-image: linear-gradient(to bottom, #000 60%, transparent 100%);
  }
  .emblem-area--front { left: 478px; top: 66px; width: 375px; height: 385px; }
  .emblem-area--back-left { left: 211px; top: 244px; width: 81px; height: 162px; background: var(--emblem-blue); }
  .emblem-area--back-right { left: 634px; top: 244px; width: 80px; height: 167px; background: var(--emblem-green); }

  .brand-name {
    position: absolute; font-weight: 700; color: var(--brand-green);
    font-size: 50px; letter-spacing: 4px; line-height: 1; white-space: nowrap;
  }
  .front-brand { left: 60px; top: 180px; }
  .dealer-block { position: absolute; right: 550px; top: 232px; text-align: right; color: var(--text-light); }
  .dealer-name { font-size: 22px; font-weight: 300; line-height: 1.1; }
  .dealer-role { font-size: 14px; font-weight: 300; line-height: 1.4; letter-spacing: .2px; }
  .phone { position: absolute; right: 550px; top: 281px; display: flex; align-items: center; gap: 12px;
    color: var(--text-light); font-size: 22px; font-weight: 300; }
  .phone svg { width: 21px; height: 21px; }

  .flap { position: absolute; left: 0; top: 0; width: 922px; height: 101px; }
  .back-brand { left: 0; right: 0; top: 296px; text-align: center; }
  .back-tagline { position: absolute; left: 0; right: 0; top: 358px; text-align: center;
    color: var(--text-grey); font-size: 20px; font-weight: 300; letter-spacing: .3px; }
</style>
</head>
<body>
<main class="sheet">

  <section class="envelope envelope--front" aria-label="Envelope front">
    <div class="stripes stripes--front"></div>
    <div class="emblem-area emblem-area--front" role="img" aria-label="Large faint blue and green shield emblem with a round-the-clock icon and 24/7"></div>
    <div class="brand-name front-brand">DK Alarm</div>
    <div class="dealer-block">
      <div class="dealer-name">NORVALE</div>
      <div class="dealer-role">SECURITY PRODUCTS DEALER</div>
    </div>
    <div class="phone">
      <svg viewBox="0 0 20 20" aria-hidden="true">
        <rect width="20" height="20" rx="4" fill="var(--brand-green)"/>
        <path d="M6 4.5 L8 4.5 L9 7.5 L7.6 8.6 Q8.6 11 11.4 12.4 L12.5 11 L15.5 12 L15.5 14 Q15 15.5 13.5 15.5 Q9 15.2 6.3 12 Q4.5 9.5 4.5 6.5 Q4.6 4.8 6 4.5 Z" fill="#fff"/>
      </svg>
      <span>555 - 014 - 2290</span>
    </div>
  </section>

  <section class="envelope envelope--back" aria-label="Envelope back">
    <svg class="flap" viewBox="0 0 922 101" role="img" aria-label="Envelope flap with a repeating shield outline pattern">
      <polygon points="0,0 922,0 845,101 76,101" fill="var(--flap-teal)"/>
    </svg>
    <div class="stripes stripes--left"></div>
    <div class="stripes stripes--right"></div>
    <div class="emblem-area emblem-area--back-left" role="img" aria-label="Faint blue half of a shield emblem"></div>
    <div class="emblem-area emblem-area--back-right" role="img" aria-label="Faint green half of a shield emblem"></div>
    <div class="brand-name back-brand">DK Alarm</div>
    <div class="back-tagline">SECURITY PRODUCTS DEALER</div>
  </section>

</main>
</body>
</html>
```